Danielle Brooke Interiors business cards

We need a DOUBLE SIDED business card design that is simple, elegant and modern. We are a rapidly growing Interior Design Firm, and our brand colours are blush pink, navy, and antique gold, so we require some or all of these colours to be used. The final design should portray elegance, simplicity, and have a modern feel. We have upload inspiration photos that have the feel we're looking for.

Industry/Entity Type

Interior Design

Contact Information for Business Card

Contact information and LOGO

Colors
EB3D1F
EC4F4E
F09395
F8D3D4
FCEDEE

Requirements
Must have
• Navy, the right shade of blush pink, and antique gold

```html
<!DOCTYPE html>
<html lang="en">
<head>
<meta charset="utf-8">
<title>Danielle Brooke Interiors – Business Cards</title>
<link rel="stylesheet" href="https://fonts.googleapis.com/css2?family=Jost:wght@400&family=Poppins:wght@400;500;700&display=swap">
<style>
  :root {
    --navy: #0f2566;
    --navy-deep: #061a47;
    --blush: #e3b2ae;
    --blush-light: #f3d3cb;
    --blush-soft: #fae6df;
    --gold: #a98a3f;
    --gold-line: #c9a54a;
    --ink: #1c1c2a;
    --paper: #ffffff;
  }
  * { box-sizing: border-box; margin: 0; padding: 0; }
  html, body { width: 1200px; height: 2518px; overflow: hidden; background: var(--paper); }
  .canvas { position: relative; width: 1200px; height: 2518px; }
  .card {
    position: absolute; left: 160px; width: 880px; height: 503px;
    background: var(--paper); overflow: hidden;
    box-shadow: 0 10px 30px rgba(0,0,0,0.28);
  }
  .card--front { top: 726px; }
  .card--back { top: 1289px; }
  .card__art { position: absolute; inset: 0; width: 880px; height: 503px; }
  .brand-mark {
    position: absolute; left: 110px; top: 150px; width: 440px;
    font-family: "Jost", sans-serif; font-weight: 400; color: var(--gold);
    text-align: center; line-height: 1.15;
  }
  .brand-mark__line { display: block; font-size: 46px; letter-spacing: 1px; }
  .brand-mark__line--sub { font-size: 46px; letter-spacing: 6px; }
  .brand-mark--small {
    left: 50px; top: 200px; width: 300px; font-size: 25px; letter-spacing: 0.5px;
  }
  .contact { position: absolute; left: 390px; top: 148px; font-family: "Poppins", sans-serif; }
  .contact__name { color: var(--navy); font-weight: 700; font-size: 33px; letter-spacing: 0.5px; line-height: 1; }
  .contact__title { color: var(--ink); font-weight: 400; font-size: 13.5px; letter-spacing: 2px; margin-top: 8px; }
  .contact__list { list-style: none; margin-top: 22px; }
  .contact__item { display: flex; align-items: center; gap: 12px; height: 46px; color: var(--ink); font-size: 19px; }
  .contact__item--phone { color: var(--navy); font-weight: 700; font-size: 31px; }
  .contact__icon {
    width: 36px; height: 36px; border-radius: 6px; background: var(--blush);
    display: flex; align-items: center; justify-content: center; flex: none;
  }
</style>
</head>
<body>
<main class="canvas">

  <section class="card card--front" aria-label="Business card front">
    <svg class="card__art" viewBox="0 0 880 503" aria-hidden="false">
      <polygon points="663,0 880,0 880,320" fill="var(--navy)"/>
      <polygon points="800,0 880,0 880,320 752,122" fill="var(--navy-deep)"/>
      <polygon points="740,105 880,320 880,503 610,503" fill="var(--blush)"/>
      <polygon points="680,280 880,280 880,503 610,503" fill="url(#frontWash)" role="img" aria-label="Blush watercolour texture"/>
      <line x1="775" y1="0" x2="583" y2="503" stroke="var(--gold-line)" stroke-width="3"/>
      <line x1="800" y1="0" x2="610" y2="503" stroke="var(--gold-line)" stroke-width="3"/>
      <defs>
        <radialGradient id="frontWash" cx="0.65" cy="0.45" r="0.7">
          <stop offset="0" stop-color="#d3aaa6"/>
          <stop offset="0.45" stop-color="var(--blush-light)"/>
          <stop offset="1" stop-color="var(--blush-soft)"/>
        </radialGradient>
      </defs>
    </svg>
    <div class="brand-mark">
      <span class="brand-mark__line">DANIELLE BROOKE</span>
      <span class="brand-mark__line brand-mark__line--sub">INTERIORS</span>
    </div>
  </section>

  <section class="card card--back" aria-label="Business card back">
    <svg class="card__art" viewBox="0 0 880 503">
      <defs>
        <linearGradient id="backWash" x1="0" y1="0" x2="0.3" y2="1">
          <stop offset="0" stop-color="var(--blush-light)"/>
          <stop offset="1" stop-color="var(--blush-soft)"/>
        </linearGradient>
      </defs>
      <polygon points="773,0 880,0 880,160" fill="var(--navy)"/>
      <polygon points="880,175 880,503 752,503" fill="var(--blush)"/>
      <polygon points="880,330 880,503 752,503 818,330" fill="url(#backWash)" role="img" aria-label="Blush watercolour texture"/>
      <line x1="880" y1="92" x2="725" y2="503" stroke="var(--gold-line)" stroke-width="3"/>
      <line x1="880" y1="160" x2="750" y2="503" stroke="var(--gold-line)" stroke-width="3"/>
    </svg>

    <div class="brand-mark brand-mark--small">DANIELLE BROOKE INTERIORS</div>

    <div class="contact">
      <h1 class="contact__name">DANIELLE BROOKE</h1>
      <p class="contact__title">INTERIOR DESIGNER &amp; DECORATOR</p>
      <ul class="contact__list">
        <li class="contact__item contact__item--phone">
          <span class="contact__icon">
            <svg width="22" height="22" viewBox="0 0 24 24" fill="none" stroke="var(--navy)" stroke-width="2" stroke-linecap="round" stroke-linejoin="round"><path d="M5 4h4l2 5-2.5 1.5a11 11 0 0 0 5 5L15 13l5 2v4a2 2 0 0 1-2 2A16 16 0 0 1 3 6a2 2 0 0 1 2-2"/></svg>
          </span>
          905-555-0142
        </li>
        <li class="contact__item">
          <span class="contact__icon">
            <svg width="22" height="22" viewBox="0 0 24 24" fill="none" stroke="var(--navy)" stroke-width="2" stroke-linecap="round" stroke-linejoin="round"><path d="M12 21s-6-6-6-11a6 6 0 0 1 12 0c0 5-6 11-6 11z"/><circle cx="12" cy="10" r="2.2"/></svg>
          </span>
          Lakeview ON | L4B 2K7
        </li>
        <li class="contact__item">
          <span class="contact__icon">
            <svg width="22" height="22" viewBox="0 0 24 24" fill="none" stroke="var(--navy)" stroke-width="2"><circle cx="12" cy="12" r="9"/><path d="M3 12h18M12 3c3 3 3 15 0 18M12 3c-3 3-3 15 0 18"/></svg>
          </span>
          www.daniellebrookeinteriors.com
        </li>
      </ul>
    </div>
  </section>

</main>
</body>
</html>
```